Consulting business card

*1) An Overview:* The business is simply a financial transaction wherein I
offer to provide advice to financial holders of commercial real estate
mortgages (which are sub-performing or non-performing), and said holders
are desirous of selling said mortgages which I will offer advice to said
holders in the purchase of said mortgages. Please note the attached copy
of a proposed line-by-line business card which starts with the 1st line
"RKW Advisory, LLC" with the 2nd line "Purchase of Commercial Mortgage
Loan" and the 3rd line "Sub-performing and Non-performing" is my desired
copy subject to any suggested changes. Please ignore the the copy below
the aforementioned proposed card/copy as it will be activated at a later
date.and advise
*2) The Target Market:* I contact and advise senior officers in banks,
insurance companies, and financial institutions such as CEOs, CFOs, COOs,
and Loan Mitigation Officers: the senior officers are tasked with the
removal of sub-performing and non-performing commercial real estate loans
from their real estate portfolios. The desired market is targeted at $1-10
million USD and located in the US.
*3) Design Specifics: *STYLE should be conservative and be representative
of the financial market contacts; COLOR might show a rich forest green
element, a gold foil accent, and subtle black printing, however,
alternatively, silver foil accent(s) with strong black print would seem in
harmony with the services offered, however, I would appreciate any artful
suggestions; IMAGERY should be subtle (no logo can be strong enough to make
an immediate impact): the quality should make the recipient feel he/she has
just met an experienced and competent financial adviser (I have over 55
years of successful financial and business experience).
720.217.6154davidfredrickjones@gmail.com

```html
<!DOCTYPE html>
<html lang="en">
<head>
<meta charset="utf-8">
<title>RKW Advisory, LLC – Business Card</title>
<link rel="stylesheet" href="https://fonts.googleapis.com/css2?family=Tinos&family=Arimo&display=swap">
<style>
  :root {
    --backdrop: #e9e7e2;
    --forest-green: #1f8a42;
    --gold: #cdb93c;
    --ink: #151515;
    --ink-soft: #2a2a2a;
    --light-text: #f3f6f1;
  }
  html, body {
    margin: 0;
    padding: 0;
    width: 1200px;
    height: 892px;
    overflow: hidden;
    background: var(--backdrop);
  }
  .canvas {
    position: relative;
    width: 1200px;
    height: 892px;
  }
  .business-card {
    position: absolute;
    left: 150px;
    top: 189px;
    width: 900px;
    height: 514px;
    border-radius: 34px;
    overflow: hidden;
    box-shadow: 0 14px 40px rgba(0,0,0,0.22);
  }
  .card-art {
    position: absolute;
    inset: 0;
    width: 100%;
    height: 100%;
  }
  .company-block {
    position: absolute;
    left: 58px;
    top: 66px;
  }
  .company-name {
    margin: 0;
    font-family: "Tinos", "Times New Roman", serif;
    font-weight: 400;
    font-size: 58px;
    line-height: 1;
    color: var(--ink);
  }
  .company-tagline {
    margin: 16px 0 0 14px;
    font-family: "Arimo", Arial, sans-serif;
    font-size: 25px;
    line-height: 1.55;
    color: var(--ink-soft);
  }
  .contact-block {
    position: absolute;
    right: 40px;
    top: 300px;
    text-align: right;
    color: var(--light-text);
  }
  .person-name {
    margin: 0 30px 18px 0;
    font-family: "Tinos", "Times New Roman", serif;
    font-size: 38px;
    line-height: 1;
  }
  .contact-line {
    display: flex;
    justify-content: flex-end;
    align-items: center;
    gap: 14px;
    margin: 0 0 12px;
    font-family: "Arimo", Arial, sans-serif;
    font-size: 21px;
  }
  .contact-icon {
    width: 20px;
    height: 20px;
    flex: none;
  }
</style>
</head>
<body>
<main class="canvas">
  <article class="business-card">
    <svg class="card-art" viewBox="0 0 900 514" aria-hidden="true">
      <defs>
        <linearGradient id="whiteFade" x1="0" y1="0" x2="0" y2="1">
          <stop offset="0" stop-color="#ffffff"/>
          <stop offset="1" stop-color="#cdcdcd"/>
        </linearGradient>
        <linearGradient id="greenFade" x1="0" y1="0" x2="1" y2="1">
          <stop offset="0" stop-color="#24954a"/>
          <stop offset="1" stop-color="#1a7b3a"/>
        </linearGradient>
      </defs>
      <rect class="gold-band" width="900" height="514" fill="var(--gold)"/>
      <path class="white-panel" d="M0 0 H600 C640 240 400 420 0 514 Z" fill="url(#whiteFade)"/>
      <path class="green-panel" d="M700 0 H900 V514 H40 C440 420 670 260 700 0 Z" fill="url(#greenFade)"/>
      <path class="divider-line" d="M700 0 C670 260 440 420 40 514" fill="none" stroke="#ffffff" stroke-width="2.5"/>
    </svg>

    <header class="company-block">
      <h1 class="company-name">RKW Advisory, LLC</h1>
      <p class="company-tagline">Purchase of Commercial Mortgage Loan<br>Sub-performing and Non-performing</p>
    </header>

    <section class="contact-block">
      <p class="person-name">Tomas Heraldwick</p>
      <p class="contact-line">
        <span class="contact-text">555.304.8827</span>
        <svg class="contact-icon" viewBox="0 0 22 22" aria-label="phone">
          <rect x="1" y="1" width="20" height="20" rx="2" fill="#ffffff"/>
          <path d="M7 5 L9 5 L10 8 L8.5 9.5 C9.5 11.5 10.5 12.5 12.5 13.5 L14 12 L17 13 L17 15 C17 16 16 17 15 17 C10 16.5 5.5 12 5 7 C5 6 6 5 7 5 Z" fill="var(--forest-green)"/>
        </svg>
      </p>
      <p class="contact-line">
        <span class="contact-text">tomasheraldwick@mailbox.example</span>
        <svg class="contact-icon" viewBox="0 0 22 22" aria-label="email">
          <rect x="1" y="1" width="20" height="20" rx="2" fill="#ffffff"/>
          <rect x="4.5" y="6.5" width="13" height="9" fill="none" stroke="var(--forest-green)" stroke-width="1.6"/>
          <path d="M4.5 6.5 L11 12 L17.5 6.5" fill="none" stroke="var(--forest-green)" stroke-width="1.6"/>
        </svg>
      </p>
    </section>
  </article>
</main>
</body>
</html>
```